Insurance Agency website design for Brellow Cover Insurance, LP

Build a website for Brellow Cover Insurance, LP which sells Homeowners, Auto, Renters, Condo, Flood, Disability, Life, Umbrella, and health insurance. We need the coolest insurance agency website out there to get quotes, contact us, or get additional information. Please list the following insurance companies we work with: Varnix, Ostle, Meridale Mutual, Quillor, Dunmarrow, KGZ, and Pellwick.

Make a design similar to https://www.fernagentry.com/

Selling personal insurance policies

```html
<!DOCTYPE html>
<html lang="en">
<head>
<meta charset="utf-8">
<title>Brellow Cover Insurance, LP</title>
<link href="https://fonts.googleapis.com/css2?family=Lexend:wght@300;400;500;600;700&display=swap" rel="stylesheet">
<style>
:root{
  --blue:#1a6fc4;
  --blue-mid:#2d86d9;
  --navy:#0f2f74;
  --navy-deep:#0c2a66;
  --green:#6cb33f;
  --orange:#f57c00;
  --ink:#2a2f3a;
  --muted:#555d6b;
  --pale:#eaf1fa;
  --line:#d6e3f2;
  --white:#ffffff;
}
*{box-sizing:border-box;margin:0;padding:0}
html,body{width:1200px;height:4323px;overflow:hidden}
body{font-family:'Lexend',sans-serif;color:var(--ink);background:var(--white);position:relative}
.abs{position:absolute}
.eyebrow{font-size:13px;letter-spacing:2px;color:var(--green);font-weight:500;text-transform:uppercase}
.h2{font-weight:600;color:var(--blue);line-height:1.25}
.btn{position:absolute;background:var(--orange);color:#fff;border-radius:30px;font-weight:600;font-size:13px;display:flex;align-items:center;justify-content:center;gap:8px;text-transform:uppercase}
.btn::after{content:"›";font-size:18px;line-height:1}
.dash-v{position:absolute;border-left:2px dashed var(--blue-mid);width:0}
.dash-h{position:absolute;border-top:2px dashed var(--blue-mid);height:0}

/* hero */
.hero{position:absolute;left:0;top:0;width:1200px;height:727px;background:linear-gradient(180deg,#fff 0%,#eef4fb 100%);overflow:hidden}
.hero-photo{position:absolute;left:590px;top:-20px;width:720px;height:720px;border-radius:50%;background:radial-gradient(circle at 60% 40%,#4a9be6,#1a6fc4 60%,#145aa8)}
.hero-arc{position:absolute;left:572px;top:0;width:740px;height:680px;border-radius:50%;border:5px solid var(--green);border-right-color:transparent;border-top-color:transparent}
.nav{position:absolute;left:96px;top:22px;width:1032px;height:78px;background:#fff;border-radius:40px;box-shadow:0 4px 18px rgba(20,60,120,.08);display:flex;align-items:center;padding:0 30px}
.brand{display:flex;align-items:center;gap:12px;color:var(--blue);font-weight:600;font-size:17px;line-height:1.05}
.brand-mark{width:34px;height:34px;border:3px solid var(--blue);border-radius:4px}
.nav-links{display:flex;gap:40px;margin-left:80px;font-size:13px;font-weight:500;color:var(--ink)}
.nav-phone{margin-left:auto;display:flex;align-items:center;gap:8px;font-weight:500;font-size:16px}
.chip{position:absolute;background:#fff;border-radius:28px;display:flex;align-items:center;gap:10px;padding:0 22px;font-weight:500;font-size:15px;color:var(--navy);box-shadow:0 6px 18px rgba(0,0,0,.1)}
.tag{position:absolute;left:99px;top:198px;height:28px;padding:0 18px;background:var(--green);color:#fff;font-size:15px;letter-spacing:1.5px;display:flex;align-items:center;font-weight:500}
.hero h1{position:absolute;left:97px;top:236px;font-size:50px;line-height:1.03;font-weight:600;color:var(--blue)}
.hero h1 span{color:var(--navy)}
.hero-text{position:absolute;left:99px;top:364px;width:450px;font-size:15.3px;line-height:23px;color:var(--muted);font-weight:300}
.contact-line{display:flex;align-items:center;gap:8px;font-size:15px;font-weight:400;color:var(--ink)}

/* partners */
.partners{position:absolute;left:0;top:727px;width:1200px;height:110px;border-bottom:1px solid var(--line);background:#fff}
.partner{position:absolute;top:42px;font-size:24px;font-weight:500;color:#222;display:flex;align-items:center;gap:8px}

/* about */
.about-ring{position:absolute;left:42px;top:898px;width:554px;height:554px;border-radius:50%;border:2px solid #cfe2f5}
.about-photo{position:absolute;left:76px;top:932px;width:486px;height:486px;border-radius:50%;background:radial-gradient(circle at 50% 40%,#b9c6d4,#6d7f92)}
.badge{position:absolute;background:#fff;box-shadow:0 6px 20px rgba(0,0,0,.1);border-radius:4px;display:flex;flex-direction:column;justify-content:center}
.about-copy p{font-size:16px;line-height:23px;color:var(--muted);font-weight:300;margin-bottom:16px}

/* coverage */
.coverage{position:absolute;left:0;top:1530px;width:1200px;height:651px;background:linear-gradient(180deg,#eef3fa,#e6eef8)}
.skyline{position:absolute;left:0;bottom:0;width:1200px;height:260px;background:linear-gradient(180deg,rgba(190,205,225,0),rgba(190,205,225,.55))}
.card{position:absolute;width:154px;height:127px;background:#fff;border:1px solid var(--line);border-radius:4px;display:flex;flex-direction:column;align-items:center;justify-content:flex-end;padding-bottom:14px;font-size:14px;color:var(--blue)}
.card::before{content:"";position:absolute;left:12px;top:12px;width:18px;height:18px;border:1px solid #cfd8e4;border-radius:2px;background:#f3f6fa}
.card svg{margin-bottom:14px}

/* agent */
.agent-photo{position:absolute;left:84px;top:2408px;width:386px;height:386px;border-radius:50%;background:radial-gradient(circle at 40% 40%,#8fcf5d,#5ea634)}
.form{position:absolute;left:601px;top:2262px;width:490px;height:448px;background:#fff;border:1px solid var(--line);box-shadow:0 6px 24px rgba(20,60,120,.08)}
.form-head{height:126px;background:linear-gradient(90deg,var(--blue),#155aa8);color:#fff;font-size:19px;line-height:27px;padding:30px 40px;font-weight:400}
.field-label{position:absolute;left:44px;font-size:15px;color:var(--ink);font-weight:300}
.field{position:absolute;left:40px;width:404px;height:48px;border:1px solid var(--blue-mid);border-radius:2px;display:flex;align-items:center;gap:10px;padding-left:18px;font-size:13px;color:var(--muted)}

/* testimonials */
.testis{position:absolute;left:0;top:2819px;width:1200px;height:620px;background:linear-gradient(180deg,#fff 0%,#fff 60%,#e8eff8 100%)}
.tcard{position:absolute;top:3004px;width:316px;height:258px;background:#fff;border:1px solid var(--line);box-shadow:0 4px 16px rgba(20,60,120,.06);padding:28px 30px}
.quote-mark{font-size:50px;color:#a9c8ea;font-weight:700;line-height:30px;height:34px}
.tcard p{font-size:13.2px;line-height:21px;font-style:italic;color:#333;margin-top:10px}
.tfoot{display:flex;align-items:center;gap:10px;margin-top:14px}
.avatar{width:36px;height:36px;border-radius:50%;background:#c9b8a6}
.tname{font-size:11.5px;font-weight:600;color:#222}
.stars{color:var(--orange);font-size:15px;letter-spacing:5px}
.gdot{margin-left:auto;width:22px;height:22px;border-radius:50%;background:#dfe6ef}

/* quote + footer */
.footer{position:absolute;left:0;top:3822px;width:1200px;height:501px;background:linear-gradient(180deg,var(--navy),var(--navy-deep))}
.quote-card{position:absolute;left:97px;top:3403px;width:1003px;height:487px;background:linear-gradient(180deg,#1a6fc4,#1762b3);border-radius:90px 0 90px 0;color:#fff;text-align:center}
.quote-inner{position:absolute;left:12px;top:12px;right:12px;bottom:12px;border:1px solid rgba(255,255,255,.35);border-radius:80px 0 80px 0}
.quote-card p{font-size:16px;line-height:23px;font-weight:300;width:820px;margin:0 auto 14px}
.fcol h4{font-size:16px;font-weight:600;color:#fff;border-left:2px solid var(--green);padding-left:20px;height:18px;line-height:18px;margin-bottom:18px}
.fcol ul{list-style:none;padding-left:22px}
.fcol li{font-size:13px;color:#dfe8f6;line-height:26px;font-weight:300}
.social{width:24px;height:24px;border-radius:50%;background:#fff}
</style>
</head>
<body>

<!-- HERO -->
<section class="hero">
  <div class="hero-arc"></div>
  <div class="hero-photo" role="img" aria-label="Smiling woman in glasses and a light blue sweater pointing toward the coverage labels, city skyline behind"></div>

  <nav class="nav">
    <div class="brand"><span class="brand-mark"></span><span>BRELLOW COVER<br>INSURANCE, LP</span></div>
    <div class="nav-links"><span>GET INSURANCE ⌄</span><span>PERSONAL ⌄</span><span>WHY US</span></div>
    <div class="nav-phone">
      <svg width="18" height="18" viewBox="0 0 24 24"><path fill="#6cb33f" d="M6.6 10.8a15 15 0 006.6 6.6l2.2-2.2a1 1 0 011-.25 11.4 11.4 0 003.6.57 1 1 0 011 1V20a1 1 0 01-1 1A17 17 0 013 4a1 1 0 011-1h3.5a1 1 0 011 1c0 1.25.2 2.45.57 3.6a1 1 0 01-.25 1z"/></svg>
      (612) 555-0148
    </div>
    <div class="btn" style="position:static;width:144px;height:40px;margin-left:30px;font-size:12px">Get a Quote</div>
  </nav>

  <div class="tag">BRELLOW COVER INSURANCE LP</div>
  <h1>Protecting What<br><span>Matters Most</span></h1>
  <p class="hero-text">At Brellow Cover Insurance, we understand that your peace of mind is invaluable. Our mission is to protect what matters most to you—your home, your vehicle, your health, and your loved ones. With our comprehensive range of insurance solutions, we are dedicated to safeguarding your assets and providing you with the security you deserve.</p>
  <div class="abs" style="left:99px;top:550px;font-size:15px;font-weight:500">For inquiries, please contact us at</div>
  <div class="abs contact-line" style="left:99px;top:589px">
    <svg width="18" height="18" viewBox="0 0 24 24"><path fill="#1a6fc4" d="M6.6 10.8a15 15 0 006.6 6.6l2.2-2.2a1 1 0 011-.25 11.4 11.4 0 003.6.57 1 1 0 011 1V20a1 1 0 01-1 1A17 17 0 013 4a1 1 0 011-1h3.5a1 1 0 011 1c0 1.25.2 2.45.57 3.6a1 1 0 01-.25 1z"/></svg>
    (612) 555-0148
  </div>
  <div class="abs contact-line" style="left:294px;top:589px">
    <svg width="20" height="16" viewBox="0 0 24 18"><rect x="1" y="1" width="22" height="16" rx="2" fill="#1a6fc4"/><path d="M2 2l10 8 10-8" stroke="#fff" stroke-width="2" fill="none"/></svg>
    info@BrellowCover.com
  </div>

  <div class="chip" style="left:596px;top:428px;height:50px">
    <svg width="22" height="20" viewBox="0 0 24 22"><path d="M2 11L12 2l10 9M5 9v11h14V9" stroke="#6cb33f" stroke-width="2" fill="none"/></svg>Protect Home</div>
  <div class="chip" style="left:990px;top:398px;height:48px;background:var(--green);color:#fff">
    <svg width="24" height="20" viewBox="0 0 24 22"><path d="M12 20S2 13 2 7a5 5 0 0110-1 5 5 0 0110 1c0 6-10 13-10 13z" stroke="#fff" stroke-width="2" fill="none"/></svg>Your Health</div>
  <div class="chip" style="left:914px;top:596px;height:50px">
    <svg width="28" height="20" viewBox="0 0 30 20"><path d="M3 14h24v-4l-4-5H9l-4 5H3z" stroke="#1a6fc4" stroke-width="2" fill="none"/><circle cx="9" cy="15" r="2.5" fill="#1a6fc4"/><circle cx="22" cy="15" r="2.5" fill="#1a6fc4"/></svg>Protect Vehicle</div>
</section>

<!-- PARTNERS -->
<section class="partners">
  <div class="partner" style="left:84px;letter-spacing:4px;font-size:20px">VARNIX</div>
  <div class="partner" style="left:277px;letter-spacing:6px;font-size:24px">OSTLE</div>
  <div class="partner" style="left:420px;color:var(--orange)">Meridale Mutual</div>
  <div class="partner" style="left:727px;color:var(--navy)">Quillor</div>
  <div class="partner" style="left:998px;color:#c8102e;font-weight:700">KGZ</div>
</section>

<!-- ABOUT -->
<section>
  <div class="about-ring"></div>
  <div class="about-photo" role="img" aria-label="Smiling insurance agent in a grey blazer holding a tablet"></div>
  <div class="badge" style="left:30px;top:1133px;width:171px;height:76px;align-items:center;font-size:16px;line-height:20px">
    <span style="color:var(--blue);font-weight:600">FULL SERVICE</span><span style="font-weight:500">INSURANCE</span></div>
  <div class="badge" style="left:346px;top:1230px;width:150px;height:112px;padding-left:32px;font-size:16px;line-height:20px">
    <span style="color:var(--green);font-size:26px;font-weight:600;line-height:32px">500+</span><span>FIND BEST</span><span>AGENTS</span></div>

  <div class="abs eyebrow" style="left:601px;top:915px">WHO WE ARE</div>
  <h2 class="abs h2" style="left:601px;top:935px;font-size:37px">About Brellow Cover<br>Insurance, LP</h2>
  <div class="dash-h" style="left:886px;top:1003px;width:314px"></div>
  <div class="abs about-copy" style="left:601px;top:1040px;width:540px">
    <p>Brellow Cover Insurance is a full-service, independent insurance agency with over three decades of experience in delivering comprehensive insurance solutions to individuals.</p>
    <p>We proudly offer a diverse portfolio of products from more than 20 of the most reputable and financially secure companies in the industry. Our dedicated team of over 50 skilled professionals is committed to customizing these products and services to meet the unique needs of each client.</p>
    <p>At Brellow Cover Insurance, our experts are focused on addressing the individual needs of our clients, ensuring exceptional service and support at every step</p>
  </div>
  <div class="btn" style="left:592px;top:1352px;width:174px;height:44px">Get a Quote</div>
  <svg class="abs" style="left:590px;top:1438px" width="130" height="152"><path d="M120 2v46H12v102" stroke="#2d86d9" stroke-width="2" stroke-dasharray="6 5" fill="none"/></svg>
</section>

<!-- COVERAGE -->
<section class="coverage">
  <div class="skyline" role="img" aria-label="Faint city skyline silhouette"></div>
  <div class="abs eyebrow" style="left:0;width:1200px;text-align:center;top:72px">GET STARTED NOW</div>
  <h2 class="abs h2" style="left:0;width:1200px;text-align:center;top:92px;font-size:32px;line-height:42px">Now more Specifically, what type of<br>Personal Protection are you looking for?</h2>
  <div class="abs" style="left:0;width:1200px;text-align:center;top:195px;font-size:17px;font-weight:400">Select up to three coverages</div>

  <div class="card" style="left:247px;top:240px"><svg width="64" height="34" viewBox="0 0 64 34"><path d="M4 24h56v-8l-8-3-10-8H20l-8 8-8 2z" stroke="#1a6fc4" stroke-width="2" fill="none"/><circle cx="16" cy="25" r="5" fill="#fff" stroke="#1a6fc4" stroke-width="2"/><circle cx="48" cy="25" r="5" fill="#fff" stroke="#1a6fc4" stroke-width="2"/></svg>Auto</div>
  <div class="card" style="left:431px;top:240px"><svg width="46" height="40" viewBox="0 0 46 40"><path d="M4 20L23 4l19 16M9 16v22h28V16M19 38V26h8v12" stroke="#1a6fc4" stroke-width="2" fill="none"/></svg>Home</div>
  <div class="card" style="left:616px;top:240px"><svg width="44" height="44" viewBox="0 0 44 44"><circle cx="30" cy="14" r="9" stroke="#1a6fc4" stroke-width="2" fill="none"/><path d="M24 20L6 38l4 4M12 32l4 4" stroke="#1a6fc4" stroke-width="2" fill="none"/></svg>Renters</div>
  <div class="card" style="left:802px;top:240px"><svg width="44" height="44" viewBox="0 0 44 44"><path d="M6 42V8h16v34M22 16h16v26M10 14h4m4 0h0M10 22h4M10 30h4M26 24h4m4 0h0M26 32h4" stroke="#1a6fc4" stroke-width="2" fill="none"/></svg>Condo</div>
  <div class="card" style="left:247px;top:391px"><svg width="48" height="42" viewBox="0 0 48 42"><path d="M4 18a20 14 0 0140 0zM24 4v2" stroke="#1a6fc4" stroke-width="2" fill="none"/><circle cx="14" cy="26" r="3" stroke="#1a6fc4" stroke-width="2" fill="none"/><circle cx="24" cy="26" r="3" stroke="#1a6fc4" stroke-width="2" fill="none"/><circle cx="34" cy="26" r="3" stroke="#1a6fc4" stroke-width="2" fill="none"/><path d="M8 40a6 6 0 0112 0M18 40a6 6 0 0112 0M28 40a6 6 0 0112 0" stroke="#1a6fc4" stroke-width="2" fill="none"/></svg>Umbrella</div>
  <div class="card" style="left:431px;top:391px"><svg width="58" height="40" viewBox="0 0 58 40"><path d="M4 12l46-8v30H4zM10 18h12v16M30 16h14v10H30z" stroke="#1a6fc4" stroke-width="2" fill="none"/></svg>Mobile Home</div>
  <div class="card" style="left:616px;top:391px"><svg width="62" height="40" viewBox="0 0 62 40"><path d="M4 32V6h38l10 12h6v14zM10 12h10v8H10zM26 12h10v8H26z" stroke="#1a6fc4" stroke-width="2" fill="none"/><circle cx="16" cy="33" r="4" fill="#fff" stroke="#1a6fc4" stroke-width="2"/><circle cx="46" cy="33" r="4" fill="#fff" stroke="#1a6fc4" stroke-width="2"/></svg>Motor Home</div>
  <div class="card" style="left:802px;top:391px"><svg width="62" height="40" viewBox="0 0 62 40"><circle cx="12" cy="28" r="8" stroke="#1a6fc4" stroke-width="2" fill="none"/><circle cx="50" cy="28" r="8" stroke="#1a6fc4" stroke-width="2" fill="none"/><path d="M12 28l10-14h16l12 14M26 14l-4-8h8" stroke="#1a6fc4" stroke-width="2" fill="none"/></svg>ATV</div>

  <div class="btn" style="left:510px;top:551px;width:173px;height:47px">Show More</div>
</section>

<!-- AGENT -->
<section>
  <div class="dash-h" style="left:5px;top:2294px;width:98px"></div>
  <div class="abs eyebrow" style="left:122px;top:2250px">LOOKING FOR AGENT</div>
  <h2 class="abs h2" style="left:122px;top:2270px;font-size:34px;line-height:47px">Find&nbsp; the right local<br>Agent for you</h2>
  <div class="agent-photo" role="img" aria-label="Woman holding an open laptop in front of a green circle with a house behind"></div>
  <svg class="abs" style="left:500px;top:2680px" width="160" height="100"><path d="M10 20c30 0 30-20 22-10-8 12 10 58 70 60 20 0 40-12 50-26" stroke="#2d86d9" stroke-width="1.5" stroke-dasharray="4 4" fill="none"/><path d="M146 38l8-4-1 10z" fill="#1a6fc4"/></svg>

  <div class="form">
    <div class="form-head">Just some basic information. The address of your personal property will help in finding the right local agent for you.</div>
    <div class="field-label" style="top:168px">Enter the address of your insurable property</div>
    <div class="field" style="top:194px"><svg width="16" height="12" viewBox="0 0 16 12"><rect width="16" height="12" rx="1" fill="#8fb4de"/></svg>Email address</div>
    <div class="field-label" style="top:268px">Zip code (require)</div>
    <div class="field" style="top:288px"><svg width="12" height="16" viewBox="0 0 12 16"><path d="M6 16S0 9 0 6a6 6 0 0112 0c0 3-6 10-6 10z" fill="#8fb4de"/></svg>Type Zip code</div>
    <div class="btn" style="left:36px;top:358px;width:172px;height:48px;font-size:14px">Next Step</div>
  </div>
  <div class="dash-v" style="left:600px;top:2800px;height:52px"></div>
</section>

<!-- TESTIMONIALS -->
<section class="testis"></section>
<div class="abs eyebrow" style="left:0;width:1200px;text-align:center;top:2896px">TESTIMONIALS</div>
<h2 class="abs h2" style="left:0;width:1200px;text-align:center;top:2916px;font-size:33px">What Our Client Says about us</h2>

<div class="tcard" style="left:111px">
  <div class="quote-mark">“</div>
  <p>"Lorem ipsum dolor sit amet, consectetur adipiscing elit, sed do eiusmod tempor incididunt ut labore et dolore magna aliqua. Ut enim ad minim veniam, quis nostrud exercitation"</p>
  <div class="tfoot"><div class="avatar" role="img" aria-label="Client portrait"></div><div><div class="tname">Dalvin Morrow</div><div class="stars">★★★★★</div></div><div class="gdot"></div></div>
</div>
<div class="tcard" style="left:448px">
  <div class="quote-mark">“</div>
  <p>"Lorem ipsum dolor sit amet, consectetur adipiscing elit, sed do eiusmod tempor incididunt ut labore et dolore magna aliqua. Ut enim ad minim veniam, quis nostrud exercitation"</p>
  <div class="tfoot"><div class="avatar" role="img" aria-label="Client portrait"></div><div><div class="tname">Dalvin Morrow</div><div class="stars">★★★★★</div></div><div class="gdot"></div></div>
</div>
<div class="tcard" style="left:785px">
  <div class="quote-mark">“</div>
  <p>"Lorem ipsum dolor sit amet, consectetur adipiscing elit, sed do eiusmod tempor incididunt ut labore et dolore magna aliqua. Ut enim ad minim veniam, quis nostrud exercitation"</p>
  <div class="tfoot"><div class="avatar" role="img" aria-label="Client portrait"></div><div><div class="tname">Dalvin Morrow</div><div class="stars">★★★★★</div></div><div class="gdot"></div></div>
</div>
<div class="abs" style="left:515px;top:3299px;width:42px;height:3px;background:var(--blue)"></div>
<div class="abs" style="left:578px;top:3299px;width:42px;height:3px;background:#b9d1ec"></div>
<div class="abs" style="left:641px;top:3299px;width:42px;height:3px;background:#b9d1ec"></div>

<!-- FOOTER + QUOTE -->
<footer class="footer"></footer>
<section class="quote-card">
  <div class="quote-inner"></div>
  <div style="position:relative;padding-top:80px">
    <div style="font-size:13px;letter-spacing:2px;font-weight:400">CONTACT US</div>
    <div style="font-size:37px;font-weight:600;margin:8px 0 22px">Get a Quote</div>
    <p>We believe that securing your home is one of the most important decisions you can make. Obtaining a comprehensive insurance quote is essential to understanding your coverage options and ensuring that your property is adequately protected against unforeseen events.</p>
    <p>Our team of experienced professionals is here to guide you through the process, helping you find the right policy that meets your specific needs and budget. Don't leave your home's safety to chance—get a quote today and take the first step towards peace of mind.</p>
  </div>
  <div class="btn" style="left:408px;top:344px;width:200px;height:47px;font-size:16px">Get a Quote</div>
</section>
<div class="dash-v" style="left:600px;top:3406px;height:50px;border-color:rgba(255,255,255,.6)"></div>

<div class="abs" style="left:141px;top:3960px;width:260px">
  <div class="brand" style="color:#fff;font-size:17px"><span class="brand-mark" style="border-color:#fff"></span><span>BRELLOW COVER<br>INSURANCE, LP</span></div>
  <p style="font-size:11px;line-height:15px;color:#cfdcf0;margin-top:18px;font-weight:300">Lorem ipsum dolor sit amet, consectetur adipiscing elit, sed do eiusmod tempor incididunt ut labore et dolore</p>
  <div style="display:flex;gap:24px;margin-top:18px"><span class="social" aria-label="Social profile"></span><span class="social" aria-label="Social profile"></span><span class="social" aria-label="Social profile"></span></div>
</div>
<div class="abs fcol" style="left:420px;top:3972px"><h4>NAVIGATION</h4><ul><li>Home</li><li>About Us</li><li>Insurance</li><li>Services</li><li>Testimonials</li></ul></div>
<div class="abs fcol" style="left:636px;top:3970px"><h4>INSURANCE</h4><ul><li>Auto Insurance</li><li>Home Insurance</li><li>Life Insurance</li><li>Car Insurance</li><li>Business Insurance</li></ul></div>
<div class="abs fcol" style="left:861px;top:3972px"><h4>CONTACT US</h4>
  <div style="padding-left:22px;font-size:13px;color:#dfe8f6;line-height:20px;font-weight:300">
    <div style="display:flex;gap:14px"><svg width="16" height="16" viewBox="0 0 24 24"><path fill="#fff" d="M6.6 10.8a15 15 0 006.6 6.6l2.2-2.2a1 1 0 011-.25 11.4 11.4 0 003.6.57 1 1 0 011 1V20a1 1 0 01-1 1A17 17 0 013 4a1 1 0 011-1h3.5a1 1 0 011 1c0 1.25.2 2.45.57 3.6a1 1 0 01-.25 1z"/></svg><div>Phone Number<br>(612) 555-0148</div></div>
    <div style="display:flex;gap:14px;margin-top:22px"><svg width="16" height="12" viewBox="0 0 24 18"><rect x="1" y="1" width="22" height="16" rx="2" fill="#fff"/><path d="M2 2l10 8 10-8" stroke="#0f2f74" stroke-width="2" fill="none"/></svg><div>Email address<br>info@BrellowCover.com</div></div>
  </div>
</div>
<div class="abs" style="left:0;top:4212px;width:1200px;border-top:1px solid rgba(255,255,255,.15)"></div>
<div class="abs" style="left:136px;top:4250px;font-size:12px;color:#dfe8f6;font-weight:300">© 2025 Brellow Cover Insurance, LP.&nbsp; All Rights Reserved</div>
<div class="abs" style="left:861px;top:4247px;font-size:12px;color:#dfe8f6;font-weight:300;word-spacing:2px">Terms of use&nbsp;&nbsp; Privacy Policy&nbsp;&nbsp; Sitemap</div>

</body>
</html>
```